Investment company needing business card

We are wanting a business card which looks sharp and easy on the eye. We are thinking of having a business card with the logo embossed on it, to really make it stand out. We will only have a small amount of information of the business card, person's name, position, email address and phone number

Contact Information for Business Card

Danielle Frost
Executive Assistant
+64 21 473 5162
danielf@harwickpartners.co.nz

Requirements
Must have
• Embossed logo
Should not have
• Not to be busy

```html
<!DOCTYPE html>
<html lang="en">
<head>
<meta charset="utf-8">
<title>Harwick Partners – Business Card</title>
<link href="https://fonts.googleapis.com/css2?family=Source+Sans+3:wght@400;600;700&display=swap" rel="stylesheet">
<style>
  :root {
    --backdrop: #e0e0e0;
    --card: #323232;
    --green: #23b574;
    --white: #ffffff;
    --ink: #555555;
  }
  * { box-sizing: border-box; margin: 0; padding: 0; }
  html, body { width: 1130px; height: 1200px; overflow: hidden; }
  body {
    background: var(--backdrop);
    font-family: "Source Sans 3", sans-serif;
    position: relative;
  }
  .card {
    position: absolute;
    top: 228px;
    width: 425px;
    height: 743px;
    background: var(--card);
    border-radius: 48px;
    overflow: hidden;
  }
  .card--front { left: 127px; }
  .card--back { left: 579px; }

  .brand {
    position: absolute;
    display: flex;
    align-items: center;
    gap: 12px;
    color: var(--white);
    font-weight: 700;
    letter-spacing: 0.5px;
    white-space: nowrap;
  }
  .brand__square {
    width: 26px;
    height: 26px;
    background: var(--white);
    flex: none;
  }
  .card--front .brand {
    left: 31px;
    top: 88px;
    font-size: 34px;
  }

  .person {
    position: absolute;
    left: 35px;
    top: 476px;
  }
  .person__name {
    color: var(--green);
    font-weight: 700;
    font-size: 27px;
    line-height: 1.2;
  }
  .person__role {
    color: var(--white);
    font-size: 19px;
    line-height: 1.3;
  }

  .contact {
    position: absolute;
    left: 27px;
    top: 558px;
    width: 370px;
    list-style: none;
  }
  .contact__row {
    display: flex;
    height: 29px;
    margin-bottom: 3px;
  }
  .contact__value {
    flex: 1;
    background: var(--white);
    color: var(--ink);
    font-size: 18px;
    line-height: 29px;
    text-align: right;
    padding-right: 8px;
    border-radius: 4px 0 0 4px;
    white-space: nowrap;
  }
  .contact__label {
    width: 84px;
    margin-left: 2px;
    background: var(--green);
    color: var(--white);
    font-size: 19px;
    line-height: 29px;
    text-align: center;
    border-radius: 0 8px 0 0;
  }

  .back-bands {
    position: absolute;
    inset: 0;
  }
  .card--back .brand {
    left: 212px;
    top: 372px;
    font-size: 46px;
    transform: translate(-50%, -50%) rotate(-90deg);
  }
  .card--back .brand__square { width: 36px; height: 36px; background: var(--green); }
</style>
</head>
<body>
  <section class="card card--front">
    <div class="brand">
      <span class="brand__square"></span>
      <span class="brand__name">HARWICK PARTNERS</span>
    </div>

    <div class="person">
      <p class="person__name">DANIELLE FROST</p>
      <p class="person__role">Executive Assistant</p>
    </div>

    <ul class="contact">
      <li class="contact__row">
        <span class="contact__value">+64 21 473 5162</span>
        <span class="contact__label">Phone</span>
      </li>
      <li class="contact__row">
        <span class="contact__value">danielf@harwickpartners.co.nz</span>
        <span class="contact__label">Email</span>
      </li>
      <li class="contact__row">
        <span class="contact__value">www.harwickpartners.co.nz</span>
        <span class="contact__label">Website</span>
      </li>
    </ul>
  </section>

  <section class="card card--back">
    <svg class="back-bands" width="425" height="743" viewBox="0 0 425 743" aria-hidden="true">
      <polygon points="0,118 35,140 35,570 0,594" fill="var(--green)"/>
      <polygon points="425,124 392,146 392,574 425,598" fill="var(--green)"/>
    </svg>
    <div class="brand">
      <span class="brand__square"></span>
      <span class="brand__name">HARWICK PARTNERS</span>
    </div>
  </section>
</body>
</html>
```